CoinHarbor.com Site Redesign

We are looking to redesign our CoinHarbor.com site. This site is focused on helping consumers make smart financial decisions. We provide reviews and articles in various categories.

We are looking for a responsive design to run on wordpress. We will also have adsense advertisements on our page and will want some ad spot space. We are thinking of two column design vs. single column.

Here is an example of what our competitors look like:
ShopperBeacon.org (mostly reviews vs. articles)
Homepage - https://www.shopperbeacon.example/
Category Review Listing - https://www.shopperbeacon.example/mortgage-refinance/best-mortgage-refinance
Individual Review - https://www.shopperbeacon.example/mortgage-refinance/c/loan-orchard-mortgage-refinance-review

- I like that the site is extremely clean. I like the fixed header in mobile

PilotGuide
Homepage - https://www.pilotguide.example/
Category Review Listing-https://www.pilotguide.example/auto_insurance/index.php
Individual Review- https://www.pilotguide.example/auto_insurance/drivora_review.php

Articles - https://www.pilotguide.example/blog/2017/11/20/going-on-a-holiday-road-trip-be-prepared-for-these-hazards/

What I Like? I like the two column layout in that it gives room for advertising.
What I Do NOT Like? The top navigation is a little cumbersome and old. Mobile view is not very good. Content seems a bit cluttered.

PennyMoth
Homepage - https://www.pennymoth.example
Category Review Listing - https://www.pennymoth.example/blog/insurance/best-car-insurance-companies/?trk=pm_gn1_4.0
Individual Review- https://www.pennymoth.example/blog/insurance/veloro-insurance-review/

What I Like? very clean. Like the use of white space and focus on bright color call to action buttons.
What I Do NOT Like? In mobile a lot of content is pushed below the fold because of the large image above the fold. Reviews are not well organized.

Target Market(s)

consumers interested in saving money and making smart financial decisions

Industry/Entity Type

Financial

Logo Text

CoinHarbor.com or CoinHarbor

Coding

Coded - Design and coding required

Number of Pages Required

5+ page

Font styles to use
Sans Serif

Colors

Designer to choose colors to be used in the design.

Requirements
Must have
• -responsive design
• -room for ad space in the right column
Nice to have
• -good use of white space
• -clean layouts
Should not have
• -clutter

```html
<!DOCTYPE html>
<html lang="en">
<head>
<meta charset="utf-8">
<title>CoinHarbor.com – Make Smarter Financial Decisions</title>
<link href="https://fonts.googleapis.com/css2?family=Open+Sans:ital,wght@0,400;0,600;0,700;0,800;1,400;1,600&display=swap" rel="stylesheet">
<style>
:root{
  --navy:#0f3b8c;
  --nav-active:#2f86d8;
  --heading:#163f8c;
  --brand-blue:#1b7fd6;
  --brand-blue-dark:#176fc0;
  --text:#333;
  --muted:#666;
  --panel:#e4e4e4;
  --card:#ffffff;
  --soft:#f1f1f1;
  --footer:#eeeeee;
  --bar:#2f2f2f;
  --ad-yellow:#fff200;
  --ad-red:#e3161b;
}
*{box-sizing:border-box;margin:0;padding:0}
html,body{width:1200px;height:2799px;overflow:hidden}
body{position:relative;background:#fff;font-family:"Open Sans",Arial,sans-serif;color:var(--text)}
a{color:inherit;text-decoration:none}
ul{list-style:none}
.abs{position:absolute}

/* header */
.site-header{left:0;top:0;width:1200px;height:82px}
.brand{left:131px;top:24px;display:flex;align-items:center;gap:8px}
.brand-square{width:30px;height:30px;background:var(--navy)}
.brand-name{font-size:22px;font-weight:700;color:var(--navy);letter-spacing:-.3px}
.tagline{left:502px;top:32px;font-size:13px;font-style:italic;color:#444}
.account{right:128px;top:32px;display:flex;gap:28px;font-size:13px;color:#333}
.account span{display:flex;align-items:center;gap:6px}

.main-nav{left:0;top:82px;width:1200px;height:41px;background:var(--navy)}
.main-nav ul{position:absolute;left:131px;top:0;display:flex;height:41px}
.main-nav li{height:41px;display:flex;align-items:center;color:#fff;font-size:12.5px;font-weight:600;text-transform:uppercase}
.main-nav li.active{background:var(--nav-active);width:95px;justify-content:center}
.main-nav li+li{margin-left:0}

/* hero */
.hero{left:0;top:123px;width:1200px;height:493px;background:linear-gradient(120deg,#5a6169 0%,#3d4349 40%,#2a2e33 70%,#4a4f55 100%)}
.hero-shade{inset:0;background:rgba(20,22,26,.35)}
.hero h1{left:0;width:1200px;top:150px;text-align:center;color:#fff;font-size:43px;font-weight:800;letter-spacing:.3px}
.hero h2{left:0;width:1200px;top:204px;text-align:center;color:#fff;font-size:23px;font-weight:700}
.hero .disclosure{left:0;width:1200px;top:240px;text-align:center;color:#eee;font-size:13.5px;font-style:italic}
.search{left:211px;top:273px;width:776px;height:56px;background:#fff;border-radius:2px;display:flex;align-items:center;padding:0 24px;font-size:16px}
.search b{font-weight:600;color:#222;margin-right:6px}
.search span{color:#777}
.search svg{position:absolute;right:20px;top:17px}
.hero-arrow{top:235px;width:26px;height:26px;background:rgba(0,0,0,.45);display:flex;align-items:center;justify-content:center}

/* category grid */
.category-panel{left:131px;top:681px;width:660px;height:812px;background:var(--panel)}
.category-card{position:absolute;width:299px;height:97px;background:var(--card);display:flex;align-items:center;padding-left:16px}
.category-icon{width:76px;height:76px;border:1px solid #ddd;border-radius:50%;display:flex;align-items:center;justify-content:center;margin-right:20px;flex-shrink:0}
.category-name{font-size:16px;font-weight:600;color:#333;line-height:1.2}

/* sidebar */
.about-box{left:827px;top:679px;width:239px;height:351px;background:var(--brand-blue)}
.about-box h3{padding:18px 14px 0;color:#fff;font-size:19px;font-weight:700;line-height:1.2}
.about-box .about-sub{padding:6px 14px 12px;color:#fff;font-size:12px}
.about-item{height:80px;border-top:1px solid rgba(255,255,255,.25);display:flex;padding:16px 14px 0;gap:14px;color:#fff}
.about-item:first-of-type{background:var(--brand-blue-dark)}
.about-item strong{display:block;font-size:14px;font-weight:700}
.about-item p{font-size:10.5px;line-height:1.3;opacity:.9;margin-top:2px}

.sponsor-title{left:822px;top:1062px;width:244px;height:26px;background:#f4f4f4;text-align:center;font-size:13px;font-weight:700;line-height:26px;color:#222}
.ad-native{left:827px;top:1097px;width:239px;height:187px;background:#fff;padding:12px 0 0 10px;border-left:3px solid var(--brand-blue)}
.ad-native h4{font-size:22px;font-weight:400;line-height:1.3;color:#222}
.ad-native p{font-size:15px;line-height:1.4;color:#444;margin-top:8px}
.ad-native small{position:absolute;left:10px;bottom:12px;font-size:11px;color:#777}
.ad-native .go{position:absolute;right:8px;bottom:6px;width:34px;height:34px;border:2px solid var(--brand-blue);border-radius:50%;display:flex;align-items:center;justify-content:center}
.ad-choice{width:18px;height:11px;background:#cfe6f2}
.ad-insurance{left:827px;top:1293px;width:239px;height:200px;background:#f47b20;padding:6px}
.ad-insurance .inner{width:100%;height:100%;background:#1c3c78;position:relative;color:#fff;text-align:center}
.ad-insurance .ins-brand{position:absolute;left:60px;top:8px;font-size:15px;font-weight:700;color:#fff}
.ad-insurance .badge{position:absolute;left:14px;top:4px;width:34px;height:34px;border-radius:50%;background:#e3161b}
.ad-insurance .line1{position:absolute;left:12px;right:12px;top:50px;background:#e3161b;font-size:15px;font-weight:800;padding:3px 0}
.ad-insurance .plus{position:absolute;left:0;right:0;top:78px;font-size:20px;font-weight:800}
.ad-insurance .line2{position:absolute;left:12px;right:12px;top:104px;font-size:15px;font-weight:800;background:#e3161b;padding:3px 0 0}
.ad-insurance .line2 span{display:block;font-size:11px;font-weight:600;background:#1c3c78;padding:2px 0}
.ad-insurance .price{position:absolute;left:14px;right:14px;top:146px;background:#e3161b;border:2px solid #f5c400;font-size:20px;font-weight:800;padding:2px 0}
.ad-insurance .price small{font-size:11px}

/* articles */
.section-title{font-size:21px;font-weight:600;color:var(--heading)}
.recent-title{left:131px;top:1576px}
.recommended-title{left:825px;top:1576px}
.article{position:absolute;left:131px;width:660px;height:159px;display:flex;background:var(--soft)}
.article-photo{width:240px;height:159px;flex-shrink:0}
.article-body{padding:24px 24px 0 26px}
.article-body h3{font-size:17px;font-weight:600;color:#222;line-height:1.4}
.article-body p{font-size:11.5px;line-height:1.6;color:#555;margin-top:8px}
.article-body p a{color:var(--heading);font-weight:600}
.view-all{left:131px;top:2303px;width:82px;height:39px;border:1px solid #ccc;font-size:13px;display:flex;align-items:center;justify-content:center;color:#444}

.recommended-list{left:825px;top:1614px;width:241px;height:233px;background:var(--soft);padding:16px 16px 0 20px}
.recommended-list li{display:flex;gap:14px;font-size:12.5px;line-height:1.45;color:#333;margin-bottom:16px}
.recommended-list li::before{content:"›";font-size:16px;line-height:1;color:#444}
.ad-stock{left:827px;top:1860px;width:239px;height:482px;background:var(--ad-yellow);text-align:center}
.ad-stock .headline{position:absolute;left:0;right:0;top:107px;color:var(--ad-red);font-size:31px;font-weight:800;line-height:1.5}
.ad-stock .trial{position:absolute;left:0;right:0;top:295px;font-size:20px;font-weight:700;color:#111}
.ad-stock .url{position:absolute;left:0;right:0;top:341px;font-size:19px;font-weight:700;color:#111}

/* footer */
.site-footer{left:0;top:2422px;width:1200px;height:321px;background:var(--footer)}
.footer-col{position:absolute;top:58px}
.footer-col h4{font-size:17px;font-weight:600;color:#222;margin-bottom:12px}
.footer-col li{font-size:11px;color:#444;line-height:24px}
.footer-col li::before{content:"•";margin-right:6px;color:#777}
.newsletter p{font-size:11px;line-height:1.5;color:#444;width:240px}
.newsletter .field{margin-top:12px;width:239px;height:39px;background:#fff;border:1px solid #ccc;font-size:11px;color:#888;padding:12px 14px}
.newsletter .subscribe{margin-top:10px;width:95px;height:38px;background:#333;color:#fff;font-size:12px;font-weight:600;display:flex;align-items:center;justify-content:center}
.bottom-bar{left:0;top:2743px;width:1200px;height:56px;background:var(--bar)}
.bottom-bar p{position:absolute;left:131px;top:20px;font-size:11.5px;color:#ccc}
.social{position:absolute;right:131px;top:20px;display:flex;gap:20px}
.social span{width:14px;height:14px;border-radius:50%;background:#aaa}
</style>
</head>
<body>

<header class="site-header abs">
  <a class="brand abs" href="#"><span class="brand-square"></span><span class="brand-name">CoinHarbor.com</span></a>
  <p class="tagline abs">Trusted Financial Advice and Reviews Since 2001</p>
  <div class="account abs">
    <span><svg width="13" height="13" viewBox="0 0 13 13"><path d="M1 6.5h7M5.5 3.5l3 3-3 3M8 1h4v11H8" fill="none" stroke="#333" stroke-width="1.5"/></svg>Login</span>
    <span><svg width="13" height="13" viewBox="0 0 13 13"><rect x="1" y="2" width="9" height="10" fill="none" stroke="#333" stroke-width="1.4"/><path d="M5 8l7-7" stroke="#333" stroke-width="1.6"/></svg>Register</span>
  </div>
</header>

<nav class="main-nav abs">
  <ul>
    <li class="active">Home</li>
    <li style="margin-left:46px">Annuities</li>
    <li style="margin-left:63px">Auto Insurance</li>
    <li style="margin-left:70px">Credit Monitoring</li>
    <li style="margin-left:71px">Debt Management</li>
    <li style="margin-left:76px">Motgages</li>
  </ul>
</nav>

<section class="hero abs" role="img" aria-label="Photo of a desk with a laptop, financial charts and a coffee cup">
  <div class="hero-shade abs"></div>
  <h1 class="abs">MAKE SMARTER FINANCIAL DECISIONS</h1>
  <h2 class="abs">Find the best financial products &amp; services</h2>
  <p class="disclosure abs">Disclosure: We receive advertising revenue from some partners. Learn more.</p>
  <div class="search abs"><b>I'm looking for</b><span>product or category</span>
    <svg width="22" height="22" viewBox="0 0 22 22"><circle cx="9" cy="9" r="6.5" fill="none" stroke="#163f8c" stroke-width="3"/><path d="M14 14l6 6" stroke="#163f8c" stroke-width="3.2"/></svg>
  </div>
  <div class="hero-arrow abs" style="left:0"><svg width="12" height="12" viewBox="0 0 12 12"><path d="M8 1L3 6l5 5" fill="none" stroke="#fff" stroke-width="2"/></svg></div>
  <div class="hero-arrow abs" style="right:0"><svg width="12" height="12" viewBox="0 0 12 12"><path d="M4 1l5 5-5 5" fill="none" stroke="#fff" stroke-width="2"/></svg></div>
</section>

<section class="category-panel abs">
  <a class="category-card" style="left:24px;top:22px"><span class="category-icon"><svg width="30" height="30" viewBox="0 0 30 30"><path d="M3 27h24M3 3v24" stroke="#555" stroke-width="2"/><rect x="8" y="16" width="4" height="9" fill="#555"/><rect x="14" y="11" width="4" height="14" fill="#555"/><rect x="20" y="6" width="4" height="19" fill="#555"/></svg></span><span class="category-name">Annuities</span></a>
  <a class="category-card" style="left:337px;top:22px"><span class="category-icon"><svg width="34" height="22" viewBox="0 0 34 22"><path d="M3 14l4-8h18l5 8v5H3z" fill="#555"/><circle cx="9" cy="19" r="3" fill="#fff" stroke="#555" stroke-width="2"/><circle cx="25" cy="19" r="3" fill="#fff" stroke="#555" stroke-width="2"/></svg></span><span class="category-name">Auto Insurance</span></a>

  <a class="category-card" style="left:24px;top:134px"><span class="category-icon"><svg width="34" height="24" viewBox="0 0 34 24"><rect x="1" y="1" width="32" height="22" rx="2" fill="none" stroke="#555" stroke-width="2"/><path d="M1 7h32" stroke="#555" stroke-width="3"/><path d="M5 15h12M5 19h8" stroke="#555" stroke-width="2"/></svg></span><span class="category-name">Credit Monitoring</span></a>
  <a class="category-card" style="left:337px;top:134px"><span class="category-icon"><svg width="30" height="30" viewBox="0 0 30 30"><rect x="2" y="3" width="26" height="18" fill="none" stroke="#555" stroke-width="2"/><path d="M10 12l12 14" stroke="#555" stroke-width="3"/></svg></span><span class="category-name">Credit Repair</span></a>

  <a class="category-card" style="left:24px;top:246px"><span class="category-icon"><svg width="32" height="30" viewBox="0 0 32 30"><circle cx="20" cy="9" r="7" fill="none" stroke="#555" stroke-width="2"/><path d="M2 20h6v8H2zM8 22h10l8-4 2 2-9 7H8" fill="#555"/></svg></span><span class="category-name">Debt Management</span></a>
  <a class="category-card" style="left:337px;top:246px"><span class="category-icon"><svg width="32" height="26" viewBox="0 0 32 26"><rect x="4" y="3" width="24" height="15" fill="none" stroke="#555" stroke-width="2" transform="rotate(12 16 10)"/><path d="M3 16h10l6 4v5H3z" fill="#555"/></svg></span><span class="category-name">Identity Theft</span></a>

  <a class="category-card" style="left:24px;top:358px"><span class="category-icon"><svg width="32" height="32" viewBox="0 0 32 32"><path d="M2 15a14 11 0 0 1 28 0z" fill="none" stroke="#555" stroke-width="2"/><path d="M16 15v12a3 3 0 0 1-6 0" fill="none" stroke="#555" stroke-width="2"/></svg></span><span class="category-name">Life Insurance</span></a>
  <a class="category-card" style="left:337px;top:358px"><span class="category-icon"><svg width="32" height="30" viewBox="0 0 32 30"><path d="M16 2L2 14h4v14h8v-8h4v8h8V14h4z" fill="#555"/></svg></span><span class="category-name">Mortgages</span></a>

  <a class="category-card" style="left:24px;top:470px"><span class="category-icon"><svg width="32" height="30" viewBox="0 0 32 30"><rect x="14" y="4" width="16" height="12" fill="none" stroke="#555" stroke-width="2"/><circle cx="8" cy="8" r="4" fill="#555"/><path d="M3 28V15h10v13M2 20h28" stroke="#555" stroke-width="2.5" fill="none"/></svg></span><span class="category-name">Online Brokerages</span></a>
  <a class="category-card" style="left:337px;top:470px"><span class="category-icon"><svg width="26" height="32" viewBox="0 0 26 32"><path d="M2 2h16l6 6v22H2z" fill="none" stroke="#555" stroke-width="2"/><path d="M6 12h14M6 17h14M6 22h14M6 26h8" stroke="#555" stroke-width="1.6"/></svg></span><span class="category-name">Payday Loans</span></a>

  <a class="category-card" style="left:24px;top:582px"><span class="category-icon"><svg width="22" height="32" viewBox="0 0 22 32"><text x="11" y="27" text-anchor="middle" font-family="Open Sans,Arial,sans-serif" font-size="30" font-weight="700" fill="#555">$</text></svg></span><span class="category-name">Personal Finance</span></a>
  <a class="category-card" style="left:337px;top:582px"><span class="category-icon"><svg width="32" height="32" viewBox="0 0 32 32"><circle cx="16" cy="7" r="5" fill="#555"/><path d="M3 14l13 4 13-4v14l-13 4-13-4z" fill="#555"/><path d="M16 18v14" stroke="#fff" stroke-width="1.5"/></svg></span><span class="category-name">Student Loan<br>Consolidation</span></a>

  <a class="category-card" style="left:24px;top:694px"><span class="category-icon"><svg width="30" height="32" viewBox="0 0 30 32"><path d="M2 2h18v26H2z" fill="#555"/><path d="M6 8h10M6 12h10M6 16h6" stroke="#fff" stroke-width="1.6"/><circle cx="21" cy="23" r="7" fill="#fff" stroke="#555" stroke-width="2"/><path d="M18 23l2 2 4-4" fill="none" stroke="#555" stroke-width="2"/></svg></span><span class="category-name">Tax Settlement</span></a>
</section>

<aside class="about-box abs">
  <h3>What is CoinHarbor.com?</h3>
  <p class="about-sub">Financial Service Advice and Reviews</p>
  <div class="about-item"><svg width="22" height="22" viewBox="0 0 22 22"><circle cx="9" cy="9" r="6.5" fill="none" stroke="#fff" stroke-width="3"/><path d="M14 14l6 6" stroke="#fff" stroke-width="3.2"/></svg><div><strong>We Analyze &amp; Explain</strong><p>We analyze &amp; explain how each online service works</p></div></div>
  <div class="about-item"><svg width="22" height="22" viewBox="0 0 22 22"><rect x="2" y="5" width="14" height="14" fill="none" stroke="#fff" stroke-width="2"/><path d="M8 13l11-11" stroke="#fff" stroke-width="3"/></svg><div><strong>We Test &amp; Compare</strong><p>We test &amp; compare the leading services in each category</p></div></div>
  <div class="about-item"><svg width="22" height="22" viewBox="0 0 22 22"><path d="M11 1l3 7h7l-5.5 4.5 2 7.5L11 15.5 4.5 20l2-7.5L1 8h7z" fill="#fff"/></svg><div><strong>We Review &amp; Rate</strong><p>We review and rate each service to show which is best</p></div></div>
</aside>

<div class="sponsor-title abs">Our Sponsors</div>
<div class="ad-native abs">
  <span class="ad-choice abs" style="right:0;top:-8px"></span>
  <h4>11 Superfoods<br>In 1 Glass</h4>
  <p>Get The Great Tasting Way to Improve Health, Skin, Metabolism, Energy and More!</p>
  <small>Verdalia</small>
  <span class="go"><svg width="12" height="14" viewBox="0 0 12 14"><path d="M3 1l6 6-6 6" fill="none" stroke="#1b7fd6" stroke-width="2.4"/></svg></span>
</div>
<div class="ad-insurance abs">
  <div class="inner">
    <span class="badge"></span>
    <span class="ins-brand">Meridian Life</span>
    <div class="line1">₹ 50 LAKH LIFE COVER</div>
    <div class="plus">+</div>
    <div class="line2">₹ 10 LAKH HEALTH COVER<span>for 34 major illnesses*</span></div>
    <div class="price"><small>JUST</small> ₹ 489 <small>PER MONTH</small></div>
  </div>
</div>

<h2 class="section-title recent-title abs">Recent Articles</h2>
<article class="article" style="top:1614px"><div class="article-photo" role="img" aria-label="Photo of a family sitting together at home" style="background:linear-gradient(135deg,#c9a98a,#8a6a55 60%,#5d4a3f)"></div><div class="article-body"><h3>5 “Easy” Ways Parents Can Save $1000’s a Year</h3><p>Parents, let’s face it – the high cost of raising children leaves us all needing a little extra money. Short of getting a big raise, switching jobs, or winning... <a>More</a></p></div></article>
<article class="article" style="top:1782px"><div class="article-photo" role="img" aria-label="Photo of a rider on a motorcycle on an open road" style="background:linear-gradient(160deg,#6f8a4a,#4d6234 50%,#8c8c88)"></div><div class="article-body"><h3>Motorcycle Insurance Basics</h3><p>Motorcycle insurance can be quite expensive; it can be the same amount as an auto insurance quote in some cases. Depending on the coverage... <a>More</a></p></div></article>
<article class="article" style="top:1950px"><div class="article-photo" role="img" aria-label="Photo of a toy car on insurance papers with a calculator" style="background:linear-gradient(135deg,#dfe3e8,#b9c1cb 55%,#c7534a)"></div><div class="article-body"><h3>How Do I Get Cheap Auto Insurance?</h3><p>If you’re looking for cheap auto insurance, then you aren’t alone. Many drivers regularly search for lower cost, more affordable insurance for their vehicles on a regular basis... <a>More</a></p></div></article>
<article class="article" style="top:2118px"><div class="article-photo" role="img" aria-label="Photo of a man holding car keys" style="background:linear-gradient(135deg,#8c9aa6,#5a6570 55%,#2e3338)"></div><div class="article-body"><h3>LA Car Insurance Requirements</h3><p>If you live in Louisiana you are no doubt aware that you have to carry LA auto insurance in order to legally operate a motor vehicle. However, just because... <a>More</a></p></div></article>
<a class="view-all abs">View All</a>

<h2 class="section-title recommended-title abs">Recommended Articles</h2>
<ul class="recommended-list abs">
  <li>How Do I Buy General Auto Insurance?</li>
  <li>How to Shop for Young Driver’s Insurance?</li>
  <li>Maecenas vel tortor accumsan quam varius?</li>
  <li>Aenean facilisis tincidunt lectus, id dictum nisi?</li>
</ul>
<div class="ad-stock abs">
  <div class="headline">MULTIBAGGER<br>StockSprout<br>Stock Tips</div>
  <div class="trial">30 Days FREE Trial</div>
  <div class="url">StockSprout.example</div>
</div>

<footer class="site-footer abs">
  <div class="footer-col" style="left:131px"><h4>Links</h4><ul><li>Home</li><li>Annuities</li><li>Auto Insurance</li><li>Credit Monitoring</li><li>Debt Management</li><li>Motagages</li></ul></div>
  <div class="footer-col" style="left:299px"><h4>Services</h4><ul><li>Annuities</li><li>Auto Insurance</li><li>Credit Monitoring</li><li>Credit Repair</li><li>Debt Management</li><li>Homeowners Insurance</li><li>Identity Theft</li></ul></div>
  <div class="footer-col" style="left:451px;top:92px"><ul><li>Life Insurance</li><li>Mortgages</li><li>Online Brokerages</li><li>Payday Loans</li><li>Personal Finance</li><li>Student Loan Consolidation</li></ul></div>
  <div class="footer-col" style="left:652px"><h4>Popular Services</h4><ul><li>Debt Management</li><li>Payday Loans</li><li>Credit Cards</li></ul></div>
  <div class="footer-col newsletter" style="left:826px"><h4>Newsletter</h4><p>Subscribe to our newsletter to get the latest great deals and reviews</p><div class="field">Email Address</div><div class="subscribe">SUBSCRIBE</div></div>
</footer>
<div class="bottom-bar abs">
  <p>Copyright © 2017 CoinHarbor. All rights reserved.</p>
  <div class="social"><span></span><span></span><span></span><span></span></div>
</div>

</body>
</html>
```